Tree Pruning Website

We need a website for a tree Arborist, pruning company called Maple Crest Canopy Works. We look after all types of trees, knock down trees and prune trees. Our target market is from domestic clients to government clients and everything in between.

We would like to see the use of our main colours which are orange and green

We are not looking forward in seeing a template that we have seen before but a unique template. We have designed 5 templates ourselves and we wish for the design community to take our designs to the next level.

We have also designed a template for things that **we are not** looking for (Version 4)

To make it fair for everyone, we are also not giving out any participation payments as we have had. One winner will take all of the payment!!!

I Have attached a image of the designs and a image of a tree.

We are just looking at the PSD file been developed. We have our own team who can slice the image up into a HTML format.

Target Market(s)

Everyone who needs to cut down a tree

Industry/Entity Type

Government

Requirements
Must have
• Logo on front page
A List of our services
jQuery slider on page
Phone Number on every page

```html
<!DOCTYPE html>
<html lang="en">
<head>
<meta charset="utf-8">
<title>Maple Crest Canopy Works</title>
<link href="https://fonts.googleapis.com/css2?family=Arimo:wght@400;700&family=Roboto+Condensed:wght@400;700&display=swap" rel="stylesheet">
<style>
:root{
  --yellow:#f5c400;
  --olive:#5b6f12;
  --leaf:#7fc41a;
  --leaf-bright:#8fd400;
  --grey-btn:#b3b3b3;
  --text:#555;
  --band:#f4f4ec;
  --footer:#3a4826;
  --footer-text:#e8ecd9;
  --accent-text:#f0b400;
  --black:#111;
}
*{margin:0;padding:0;box-sizing:border-box}
html,body{width:1200px;height:2243px;overflow:hidden;background:#fff}
body{position:relative;font-family:"Arimo",Arial,sans-serif;color:var(--text)}
.abs{position:absolute}
.topbar{left:0;top:0;width:1200px;height:10px;background:var(--yellow)}
.logo{left:19px;top:53px;width:331px;height:144px;border:5px solid var(--yellow);border-radius:50%;display:flex;align-items:center;justify-content:center;text-align:center;font-family:"Roboto Condensed",sans-serif;font-weight:700;font-size:30px;line-height:1.1;color:#1a1a1a;padding:0 30px}
.follow{left:630px;top:32px;font-family:"Roboto Condensed",sans-serif;font-size:26px;color:#222}
.social{top:28px;width:38px;height:38px;border-radius:50%;background:#8a8a8a}
.phone{left:1000px;font-size:17px;color:#111;display:flex;align-items:center;gap:26px}
.nav{top:176px;height:46px;display:flex;align-items:center;font-family:"Roboto Condensed",sans-serif;font-size:15px;color:#111;text-transform:uppercase}
.nav.active{background:var(--yellow);border-radius:23px;width:105px;justify-content:center;color:#fff}
.slider{left:15px;top:245px;width:1170px;height:588px;border:3px solid #ddd;border-radius:10px;background:#fff}
.slide-photo{left:31px;top:262px;width:1139px;height:558px;background:linear-gradient(180deg,#8fb7d8 0%,#6f9a4a 35%,#4f7d2a 70%,#3f6a20 100%)}
.slide-panel{left:31px;top:411px;width:489px;height:262px;background:rgba(30,30,20,.62);border-radius:0 10px 10px 0;padding:18px 24px 0 30px;color:#fff}
.slide-panel h1{font-family:"Roboto Condensed",sans-serif;font-weight:400;font-size:29px;color:var(--yellow);margin:12px 0 14px 32px}
.slide-panel p{font-size:14.5px;line-height:20px;text-align:justify}
.read-more{left:384px;top:625px;width:105px;height:29px;background:#fff;border-radius:14px;font-size:13px;color:#c88a00;display:flex;align-items:center;justify-content:center}
.dot{top:782px;width:14px;height:14px;border-radius:50%;background:#fff}
.dot.on{background:var(--yellow)}
.use h2,.panel h2,.foot h3{font-family:"Roboto Condensed",sans-serif;font-weight:400;text-transform:uppercase}
.use h2{font-size:25px;color:var(--olive);position:absolute;top:887px}
.use .photo{top:940px;width:265px;height:157px;border-radius:4px}
.use p{top:1122px;width:265px;font-size:13.6px;line-height:21px;text-align:justify;height:146px;overflow:hidden}
.btn{height:27px;width:90px;border-radius:14px;color:#fff;font-size:12px;display:flex;align-items:center;justify-content:center;text-transform:uppercase}
.btn.green{background:var(--leaf)}
.btn.grey{background:var(--grey-btn)}
.band{left:0;top:1347px;width:1200px;height:522px;background:var(--band)}
.services{left:17px;top:1391px;width:264px;height:428px;border-radius:8px;background:#7d9b4c;overflow:hidden;box-shadow:0 2px 4px rgba(0,0,0,.2)}
.services h2{height:52px;background:linear-gradient(#d9f59a,#9ed42c);color:var(--olive);font-size:24px;text-align:center;line-height:56px}
.services li{list-style:none;height:45px;border-top:1px solid #a8bf83;display:flex;align-items:center;padding-left:72px;color:#fff;font-size:18px;position:relative}
.services li::before{content:"";position:absolute;left:24px;top:17px;width:16px;height:11px;background:#5d7a30;border-radius:2px}
.services li.on{background:var(--leaf-bright)}
.services li.on::before{background:#2b3a10}
.panel h2{position:absolute;top:1396px;font-size:25px;color:var(--olive)}
.panel p{font-size:13.6px;line-height:21px;text-align:justify;height:0;overflow:hidden}
.team-photo{left:621px;top:1443px;width:260px;height:166px;background:linear-gradient(#5f8a3a,#3c5e2a)}
.thumb{width:124px;height:101px;background:linear-gradient(#6a8c45,#d9782a 60%,#4e6b30)}
.foot{left:0;top:1907px;width:1200px;height:296px;background:var(--footer);color:var(--footer-text)}
.foot h3{position:absolute;top:28px;font-size:24px;color:#fff}
.foot ul{position:absolute;top:73px;list-style:none;font-size:13.6px;line-height:22.5px}
.foot .testi{position:absolute;left:619px;top:98px;width:265px;font-size:13.6px;line-height:21px;text-align:justify}
.foot .date{position:absolute;left:820px;top:238px;font-size:12px;color:var(--leaf);font-style:italic}
.foot .contact{position:absolute;left:925px;top:98px;font-size:13.6px;line-height:22px;color:var(--accent-text)}
.copy{left:0;top:2203px;width:1200px;height:40px;background:var(--black);color:#fff;font-size:13px;display:flex;align-items:center;justify-content:center}
</style>
</head>
<body>
<div class="abs topbar"></div>
<div class="abs logo">MAPLE CREST CANOPY WORKS</div>

<div class="abs follow">Follow us :</div>
<div class="abs social" style="left:740px" aria-label="Social link"></div>
<div class="abs social" style="left:786px" aria-label="Social link"></div>
<div class="abs social" style="left:835px" aria-label="Social link"></div>

<div class="abs phone" style="top:26px">
  <svg width="24" height="22" viewBox="0 0 24 22"><path d="M2 7c0-4 20-4 20 0v3h-5V7H7v3H2z" fill="#222"/><rect x="5" y="11" width="14" height="10" rx="2" fill="#222"/><circle cx="12" cy="16" r="2.5" fill="#fff"/></svg>
  <span>0891234567</span></div>
<div class="abs phone" style="top:70px">
  <svg width="24" height="22" viewBox="0 0 24 22"><path d="M2 7c0-4 20-4 20 0v3h-5V7H7v3H2z" fill="#222"/><rect x="5" y="11" width="14" height="10" rx="2" fill="#222"/><circle cx="12" cy="16" r="2.5" fill="#fff"/></svg>
  <span>0891234567</span></div>

<div class="abs nav active" style="left:352px">Home</div>
<div class="abs nav" style="left:495px">About Us</div>
<div class="abs nav" style="left:631px">Our Services</div>
<div class="abs nav" style="left:793px">Get a Quote</div>
<div class="abs nav" style="left:938px">Our Work</div>
<div class="abs nav" style="left:1076px">Contact Us</div>

<div class="abs slider"></div>
<div class="abs slide-photo" role="img" aria-label="Arborist in safety gear with climbing rope standing on a garden lawn surrounded by trees"></div>
<div class="abs slide-panel">
  <h1>MAPLE CREST CANOPY WORKS</h1>
  <p>Lorem Ipsum is simply dummy text of the printing and typesetting industry. Lorem Ipsum has been the industry's standard dummy text ever since the 1500s, when an unknown printer took a galley of type and scrambled it to make a type specimen book. It has survived not only five centuries, but also the leap into electronic typesetting, remaining essentially unchanged. It was popularised in the 1960s with the release of</p>
</div>
<div class="abs read-more">READ MORE</div>
<div class="abs dot" style="left:57px"></div>
<div class="abs dot" style="left:80px"></div>
<div class="abs dot" style="left:103px"></div>
<div class="abs dot" style="left:126px"></div>
<div class="abs dot on" style="left:149px"></div>

<section class="use">
  <h2 style="left:19px">Domestic Use</h2>
  <h2 style="left:324px">Commercial Use</h2>
  <h2 style="left:620px">Government Use</h2>
  <h2 style="left:921px">Non Profite Use</h2>
  <div class="abs photo" style="left:17px;background:linear-gradient(#6f8f3a,#4d6a28)" role="img" aria-label="Climber pruning a tree in a domestic garden"></div>
  <div class="abs photo" style="left:319px;background:linear-gradient(#dfe8ef,#3d5b2a)" role="img" aria-label="Worker feeding a wood chipper beside a truck"></div>
  <div class="abs photo" style="left:619px;background:linear-gradient(#9fb8d0,#8a7e6a)" role="img" aria-label="Town street with shops and pedestrians"></div>
  <div class="abs photo" style="left:921px;background:linear-gradient(#5e7a3a,#8a6a45)" role="img" aria-label="Chainsaw cutting through a log"></div>
  <p class="abs" style="left:17px">Lorem Ipsum is simply dummy text of the printing and typesetting industry. Lorem Ipsum has been the industry's standard dummy text ever since the 1500s, when an unknown printer took a galley of type and scrambled it to make a type specimen book. It has survived not only five centuries, but also</p>
  <p class="abs" style="left:319px">Lorem Ipsum is simply dummy text of the printing and typesetting industry. Lorem Ipsum has been the industry's standard dummy text ever since the 1500s, when an unknown printer took a galley of type and scrambled it to make a type specimen book. It has survived not only five centuries, but also</p>
  <p class="abs" style="left:619px">Lorem Ipsum is simply dummy text of the printing and typesetting industry. Lorem Ipsum has been the industry's standard dummy text ever since the 1500s, when an unknown printer took a galley of type and scrambled it to make a type specimen book. It has survived not only five centuries, but also</p>
  <p class="abs" style="left:921px">Lorem Ipsum is simply dummy text of the printing and typesetting industry. Lorem Ipsum has been the industry's standard dummy text ever since the 1500s, when an unknown printer took a galley of type and scrambled it to make a type specimen book. It has survived not only five centuries, but also</p>
  <div class="abs btn green" style="left:17px;top:1280px">See More</div>
  <div class="abs btn grey" style="left:319px;top:1280px">See More</div>
  <div class="abs btn grey" style="left:619px;top:1280px">See More</div>
  <div class="abs btn grey" style="left:921px;top:1280px">See More</div>
</section>

<div class="abs band"></div>
<nav class="abs services">
  <h2 style="font-family:'Roboto Condensed',sans-serif;font-weight:400">OUR SERVICES</h2>
  <ul>
    <li>Diagnosis</li><li>Treatment</li><li>Purning</li><li class="on">tree Removal</li>
    <li>Stump removal</li><li>Cabeling &amp; Brancing</li><li>Arborist Consults</li><li>Tree Protection</li>
  </ul>
</nav>

<section class="panel">
  <h2 style="left:317px">About Us</h2>
  <p class="abs" style="left:317px;top:1446px;width:265px;height:330px">"But I must explain to you how all this mistaken idea of denouncing pleasure and praising pain was born and I will give you a complete account of the system, and expound the actual teachings of the great explorer of the truth, the master-builder of human happiness. No one rejects, dislikes, or avoids pleasure itself, because it is pleasure, but because those who do not know how to pursue pleasure rationally encounter consequences that are extremely painful. Nor again is there anyone who loves or pursues or desires to obtain pain of itself, because it is pain, but because occasionally circumstances occur in which toil and pain can procure him some great pleasure. To take a trivial example,</p>
  <div class="abs btn green" style="left:317px;top:1792px">See More</div>

  <h2 style="left:615px">Our Team</h2>
  <div class="abs team-photo" role="img" aria-label="Team of arborists standing together in front of a truck"></div>
  <p class="abs" style="left:617px;top:1630px;width:265px;height:145px">"But I must explain to you how all this mistaken idea of denouncing pleasure and praising pain was born and I will give you a complete account of the system, and expound the actual teachings of the great explorer of the truth, the master-builder of human happiness. No one rejects, dislikes, or avoids pleasure</p>
  <div class="abs btn green" style="left:617px;top:1792px">See More</div>

  <h2 style="left:923px">Image Gallery</h2>
  <div class="abs thumb" style="left:923px;top:1443px" role="img" aria-label="Crew in orange safety gear"></div>
  <div class="abs thumb" style="left:1059px;top:1443px" role="img" aria-label="Crew in orange safety gear"></div>
  <div class="abs thumb" style="left:923px;top:1557px" role="img" aria-label="Crew in orange safety gear"></div>
  <div class="abs thumb" style="left:1059px;top:1557px" role="img" aria-label="Crew in orange safety gear"></div>
  <div class="abs thumb" style="left:923px;top:1672px" role="img" aria-label="Crew in orange safety gear"></div>
  <div class="abs thumb" style="left:1059px;top:1672px" role="img" aria-label="Crew in orange safety gear"></div>
  <div class="abs btn green" style="left:925px;top:1792px">See More</div>
</section>

<footer class="abs foot">
  <h3 style="left:21px">Quick Links</h3>
  <ul style="left:21px"><li>Home</li><li>About us</li><li>Services</li><li>Our work</li><li>Privcy policy</li><li>Use of Terms</li></ul>
  <h3 style="left:319px">Services</h3>
  <ul style="left:319px"><li>Dignosis</li><li>Treatment</li><li>Purning</li><li>Tree Removal</li><li>Stump Removal</li><li>Cabeling &amp; Branching</li><li>Aborist Consuts</li><li>Tree Protection</li></ul>
  <h3 style="left:619px">Testimonials</h3>
  <p class="testi">"But I must explain to you how all this mistaken idea of denouncing pleasure and praising pain was born and I will give you a complete account of the system, and expound the actual teachings of the great explorer of the truth, the master-builder of human happiness.</p>
  <span class="date">25-2-2013</span>
  <h3 style="left:925px">Contact Us</h3>
  <p class="contact">41 Fernleaf Drive,<br>BRAMBLETON , WA 6021<br>Phone :08 -7720 -4418<br>Fax :&nbsp; 087720 4419</p>
</footer>
<div class="abs copy">Copyright 2013 All right recerved</div>
</body>
</html>
```